Brintel Works - Fast, Efficient and Gas Mainteance for Domestic, Commercial and Industrial clients

We are in the process of purchasing a new business and would like to get a new logo and business card.
Business is a gas maintenance business that also does new gas installations.
Has been established since 1988.
Services include:
Install all types of gas appliances & equipment inc. hot water units
Maintain / repair / replace all types of gas appliances & equipment

Target Market(s)

Domestic, Commercial and Industrial clients

Industry/Entity Type

Business

Contact Information for Business Card

admin@brintelworks.com.au
07 3918 4726
Brintel Works PTY LTD

Logo Text

Gas Fitting & Plumbing Maintenance Specialists

Font styles to use
Sans Serif

Requirements
Must have
• Logo
• Business name, contact number, email address, web address
• Domestic | Commercial | Industrial Est Since 1988
Nice to have
• Possibly a black card with a flame logo to one side
Should not have
• Spelling errors

```html
<!DOCTYPE html>
<html lang="en">
<head>
<meta charset="utf-8">
<title>Brintel Works – Business Card</title>
<link href="https://fonts.googleapis.com/css2?family=Open+Sans:wght@400;700&family=Arimo&family=Great+Vibes&display=swap" rel="stylesheet">
<style>
  :root {
    --page: #e9e6e1;
    --card-white: #f4f4f4;
    --brand-red: #e2503a;
    --title-red: #d9402b;
    --ink: #3d4148;
    --muted: #6a6d72;
    --curve-black: #111111;
    --photo-dark: #4a4c50;
    --photo-light: #b9bcc0;
  }
  * { margin: 0; padding: 0; box-sizing: border-box; }
  html, body { width: 1200px; height: 902px; overflow: hidden; background: var(--page); }
  .card {
    position: absolute; left: 100px; top: 151px;
    width: 1000px; height: 600px;
    background: var(--card-white);
    box-shadow: 0 6px 24px rgba(0,0,0,.18);
    overflow: hidden;
  }
  .card-wave { position: absolute; inset: 0; }
  .brand { position: absolute; left: 250px; top: 40px; }
  .brand-title { display: flex; align-items: flex-start; gap: 10px; }
  .brand-name {
    font-family: "Open Sans", sans-serif; font-weight: 700;
    font-size: 58px; color: var(--title-red); letter-spacing: 1px; line-height: 1;
  }
  .brand-suffix {
    font-family: "Open Sans", sans-serif; font-weight: 700;
    font-size: 12px; color: var(--ink); margin-top: 4px; white-space: nowrap;
  }
  .tagline {
    font-family: "Open Sans", sans-serif; font-weight: 700;
    font-size: 30px; color: var(--ink); margin-top: 6px; line-height: 1.2;
  }
  .sectors {
    display: flex; align-items: baseline; gap: 22px; margin-top: 4px;
    font-family: "Open Sans", sans-serif; font-size: 17px; color: var(--muted);
  }
  .established { font-family: "Great Vibes", cursive; font-size: 34px; color: var(--muted); }
  .product-photo {
    position: absolute; left: 720px; top: 250px; width: 250px; height: 220px;
    background: linear-gradient(90deg, var(--photo-dark) 0 55%, var(--photo-light) 55% 100%);
    border-radius: 6px;
  }
  .contact-list {
    position: absolute; left: 40px; top: 398px; list-style: none;
    font-family: "Arimo", sans-serif; font-size: 29px; color: #fff; line-height: 37px;
  }
  .contact-list li { display: flex; align-items: center; gap: 22px; }
  .contact-icon { width: 26px; height: 26px; flex: none; }
</style>
</head>
<body>
<div class="card">
  <svg class="card-wave" viewBox="0 0 1000 600" aria-hidden="true">
    <path d="M0 370 C 240 400, 430 340, 600 290 S 880 235, 1000 230 L1000 600 L0 600 Z" fill="var(--curve-black)"/>
    <path d="M0 383 C 240 413, 430 353, 600 303 S 880 248, 1000 243 L1000 600 L0 600 Z" fill="var(--brand-red)"/>
  </svg>

  <div class="brand">
    <div class="brand-title">
      <div class="brand-name">BRINTEL WORKS</div>
      <div class="brand-suffix">PTY LTD</div>
    </div>
    <div class="tagline">Gas fitting &amp; Plumbing Specialists</div>
    <div class="sectors">
      <span>Domestic | Commercial | Industrial</span>
      <span class="established">Est Since 1988</span>
    </div>
  </div>

  <div class="product-photo" role="img" aria-label="Photo of a gas log heater and hot water units"></div>

  <ul class="contact-list">
    <li>
      <svg class="contact-icon" viewBox="0 0 26 26"><rect width="26" height="26" rx="3" fill="#fff"/><path d="M8 6l3 0 1 4-2 1.5a9 9 0 0 0 4.5 4.5L16 14l4 1v3c0 1-1 2-2 2A13 13 0 0 1 6 8c0-1 1-2 2-2z" fill="var(--brand-red)"/></svg>
      <span>07 3918 4726</span>
    </li>
    <li>
      <svg class="contact-icon" viewBox="0 0 26 26"><rect width="26" height="26" rx="3" fill="#fff"/><rect x="6" y="9" width="14" height="10" fill="var(--brand-red)"/><rect x="9" y="5" width="8" height="5" fill="var(--brand-red)"/></svg>
      <span>07 3918 4735</span>
    </li>
    <li>
      <svg class="contact-icon" viewBox="0 0 26 26"><rect width="26" height="26" rx="3" fill="#fff"/><circle cx="13" cy="13" r="7" fill="none" stroke="var(--brand-red)" stroke-width="2"/><path d="M6 13h14M13 6c-3 4-3 10 0 14M13 6c3 4 3 10 0 14" fill="none" stroke="var(--brand-red)" stroke-width="1.5"/></svg>
      <span>www.brintelworks.com.au</span>
    </li>
    <li>
      <svg class="contact-icon" viewBox="0 0 26 26"><rect width="26" height="26" rx="3" fill="#fff"/><rect x="5" y="8" width="16" height="11" fill="var(--brand-red)"/><path d="M5 8l8 6 8-6" fill="none" stroke="#fff" stroke-width="1.5"/></svg>
      <span>admin@brintelworks.com.au</span>
    </li>
    <li>
      <svg class="contact-icon" viewBox="0 0 26 26"><rect width="26" height="26" rx="3" fill="#fff"/><path d="M13 21s-6-6-6-10a6 6 0 0 1 12 0c0 4-6 10-6 10z" fill="var(--brand-red)"/><circle cx="13" cy="11" r="2" fill="#fff"/></svg>
      <span>PO Box 2846, Coorparoo, QLD 4151</span>
    </li>
  </ul>
</div>
</body>
</html>
```